business card deign

Logo needs the following on it.
1. attached logo
2. Tagline - "If it keeps the cooler full or the good times rolling...count on us!"
3. Name- Dalton Pikes, Founder and CPO
4. Address - 412 E. Carver Avenue, Ste 2207, Brookhaven, GA. 33917
5. Phone - 555.318.4726

```html
<!DOCTYPE html>
<html lang="en">
<head>
<meta charset="utf-8">
<title>Marlowe Business Card</title>
<link href="https://fonts.googleapis.com/css2?family=Roboto:wght@400;700&display=swap" rel="stylesheet">
<style>
  :root {
    --page-bg: #262626;
    --card-bg: #1b1b1b;
    --ink: #ffffff;
    --ink-muted: #e6e6e6;
    --pattern-dark: #151515;
    --pattern-light: #3a3a3a;
    --decor-light: #2a2a2a;
  }
  * { margin: 0; padding: 0; box-sizing: border-box; }
  html, body {
    width: 1200px; height: 780px; overflow: hidden;
    background: var(--page-bg);
    font-family: "Roboto", Arial, sans-serif;
    color: var(--ink);
  }
  .canvas { position: relative; width: 1200px; height: 780px; }
  .card {
    position: absolute; left: 310px; width: 580px; height: 331px;
    border-radius: 22px; background: var(--card-bg); overflow: hidden;
    box-shadow: 0 12px 30px rgba(0,0,0,.45);
  }
  .card--back { top: 45px; }
  .card--front { top: 404px; }

  .back-pattern {
    position: absolute; inset: 0;
    background: linear-gradient(200deg, var(--pattern-light) 0%, var(--pattern-dark) 55%, var(--card-bg) 100%);
  }
  .back-brand {
    position: absolute; right: 40px; top: 148px;
    font-weight: 700; font-size: 11px; letter-spacing: 4px; color: var(--ink);
  }

  .front-decor {
    position: absolute; left: 60px; top: 40px; width: 240px; height: 291px;
    background: radial-gradient(ellipse at 50% 55%, var(--decor-light) 0%, var(--card-bg) 70%);
  }

  .brand-mark {
    position: absolute; right: 36px; top: 96px;
    display: flex; align-items: center; gap: 12px;
  }
  .brand-mark__dot { width: 18px; height: 18px; border-radius: 50%; background: var(--ink); }
  .brand-mark__name { font-weight: 700; font-size: 30px; letter-spacing: 9px; color: var(--ink); }

  .divider {
    position: absolute; left: 228px; right: 30px; top: 162px;
    height: 2px; background: var(--ink);
  }
  .person { position: absolute; left: 34px; top: 128px; }
  .person__name { font-weight: 700; font-size: 28px; line-height: 1.1; }
  .person__role { font-size: 17px; margin-top: 6px; color: var(--ink-muted); }

  .details {
    position: absolute; right: 34px; top: 178px; text-align: right;
    font-size: 12.5px; line-height: 1.45; color: var(--ink-muted);
  }
  .details__tagline { margin-bottom: 12px; }
  .details__row { display: flex; justify-content: flex-end; align-items: flex-start; gap: 8px; }
  .details__row svg { flex: none; margin-top: 2px; }
  .details__row + .details__row { margin-top: 4px; }
</style>
</head>
<body>
<main class="canvas">
  <section class="card card--back">
    <div class="back-pattern" role="img" aria-label="Repeating brand symbol pattern in graded greys"></div>
    <div class="back-brand">MARLOWE</div>
  </section>

  <section class="card card--front">
    <div class="front-decor" role="img" aria-label="Faint large brand symbol in dark grey"></div>
    <div class="brand-mark">
      <span class="brand-mark__dot"></span>
      <span class="brand-mark__name">MARLOWE</span>
    </div>
    <div class="divider"></div>
    <div class="person">
      <div class="person__name">Dalton Pikes</div>
      <div class="person__role">Founder and CPO</div>
    </div>
    <div class="details">
      <p class="details__tagline">If it keeps the cooler full or<br>the good times rolling...count on us!</p>
      <div class="details__row">
        <span>555.318.4726</span>
        <svg width="12" height="12" viewBox="0 0 24 24" fill="none" stroke="#fff" stroke-width="2.2" stroke-linecap="round" stroke-linejoin="round"><path d="M22 16.9v3a2 2 0 0 1-2.2 2 19.8 19.8 0 0 1-8.6-3.1 19.5 19.5 0 0 1-6-6A19.8 19.8 0 0 1 2.1 4.2 2 2 0 0 1 4.1 2h3a2 2 0 0 1 2 1.7c.1.9.4 1.8.7 2.7a2 2 0 0 1-.5 2.1L8 9.8a16 16 0 0 0 6 6l1.3-1.3a2 2 0 0 1 2.1-.4c.9.3 1.8.6 2.7.7a2 2 0 0 1 1.7 2z"/></svg>
      </div>
      <div class="details__row">
        <span>412 E. Carver Avenue,<br>Ste 2207, Brookhaven, GA. 33917</span>
        <svg width="12" height="14" viewBox="0 0 24 28" fill="none" stroke="#fff" stroke-width="2.2" stroke-linecap="round" stroke-linejoin="round"><path d="M12 25s-8-7.5-8-13a8 8 0 0 1 16 0c0 5.5-8 13-8 13z"/><circle cx="12" cy="12" r="3"/></svg>
      </div>
    </div>
  </section>
</main>
</body>
</html>
```